High-end law practice specializing in closely held business succession planning and complex estates

Solo practitioner whose practice specializes in high-net worth, complex estate planning needs muliple versions of letterhead black and white, please. Letterhead should incorporate slogan, "Protecting your family business is my business," for one and "Complex Estate Planning"; third with no slogan. All for The Law Office of Marcy Lynn Pettibone, PC, 418 Cedar Hollow Ln., Newport News, Virginia 23648, Tel. 757-555-0142 Fax tbd email: marcy@mlplawgroup.example; Marcy Lynn Pettibone, Esq., principal, licensed in VA, NY, DC
Updates

Project Deadline Extended
Reason: My internet service went down and I can only view designs on my smart phone -- it's just too hard to review. So sorry! Working with my ISP now. Please be patient!

Target Market(s)

High net worth clients with complex estate planning needs, family businesses, family farmers, family foresters -- people with unique estate/succession planning needs who need a specialist who understands them.

Industry/Entity Type

Business

Font styles to use
Script

Requirements
Must have
• A high-end look and feel, connoting trustworthiness, special knowledge, and expertise.

```html
<!DOCTYPE html>
<html lang="en">
<head>
<meta charset="utf-8">
<title>The Law Office of Marcy Lynn Pettibone, PC – Letterhead</title>
<link rel="stylesheet" href="https://fonts.googleapis.com/css2?family=Arimo:wght@400;700&family=PT+Sans:wght@400;700&display=swap">
<style>
  :root {
    --ink: #0d0d0d;
    --paper: #ffffff;
    --backdrop: #e9e9e9;
    --reverse: #ffffff;
  }
  * { box-sizing: border-box; margin: 0; padding: 0; }
  html, body {
    width: 1200px;
    height: 910px;
    overflow: hidden;
    background: var(--backdrop);
  }
  .letterhead {
    position: absolute;
    left: 268px;
    top: 25px;
    width: 664px;
    height: 860px;
    background: var(--paper);
    color: var(--ink);
    box-shadow: 0 2px 10px rgba(0,0,0,0.08);
  }
  .masthead {
    position: absolute;
    top: 42px;
    left: 0;
    right: 0;
  }
  .firm-name {
    margin-left: 46px;
    font-family: "Arimo", Arial, sans-serif;
    font-weight: 700;
    font-size: 20px;
    line-height: 1.05;
    letter-spacing: 0.2px;
    text-transform: uppercase;
  }
  .credential-row {
    display: flex;
    align-items: center;
    margin-top: 4px;
  }
  .credential-band {
    background: var(--ink);
    color: var(--reverse);
    font-family: "Arimo", Arial, sans-serif;
    font-size: 11px;
    line-height: 17px;
    padding: 0 8px 0 46px;
    white-space: nowrap;
  }
  .tagline {
    margin-left: 10px;
    font-family: "Arimo", Arial, sans-serif;
    font-size: 11px;
    letter-spacing: 1.2px;
    text-transform: uppercase;
    white-space: nowrap;
  }
  .rule-end {
    margin-left: auto;
    width: 20px;
    height: 17px;
    background: var(--ink);
  }
  .footer {
    position: absolute;
    left: 0;
    bottom: 24px;
    width: 62%;
  }
  .contact {
    text-align: right;
    padding-right: 18px;
    margin-bottom: 8px;
    font-family: "PT Sans", "Myriad Pro", sans-serif;
    font-size: 11.5px;
    line-height: 1.4;
  }
  .contact strong { font-weight: 700; }
  .contact .sep { margin: 0 3px; }
  .footer-rule {
    display: block;
    width: 100%;
    height: 10px;
  }
</style>
</head>
<body>
  <main class="letterhead">
    <header class="masthead">
      <h1 class="firm-name">The Law Office<br>of Marcy Lynn Pettibone, PC</h1>
      <div class="credential-row">
        <p class="credential-band">Marcy Lynn Pettibone, Esq., principal, licensed in VA, NY, DC</p>
        <p class="tagline">Complex Estate Planning</p>
        <span class="rule-end"></span>
      </div>
    </header>

    <footer class="footer">
      <address class="contact">
        418 Cedar Hollow Ln., Newport News, Virginia 23648<br>
        <strong>Tel:</strong> 757-555-0142<span class="sep">|</span><strong>Fax:</strong> 757-555-0199<span class="sep">|</span><strong>Email:</strong> marcy@mlplawgroup.example
      </address>
      <svg class="footer-rule" viewBox="0 0 412 10" preserveAspectRatio="none" aria-hidden="true">
        <rect x="0" y="5" width="412" height="5" fill="#0d0d0d"/>
        <rect x="398" y="0" width="14" height="10" fill="#0d0d0d"/>
      </svg>
    </footer>
  </main>
</body>
</html>
```